Income Tax Flyer - Updates Needed

Just need to update this flyer design and give it a new look. We would like to keep all the same wording but make it stand out a little more. Our selling point is the "Same Day Tax Advance up to $6,000"

Lending, Small Loans, Tax Services, Title Loans, Personal Loans

```html
<!DOCTYPE html>
<html lang="en">
<head>
<meta charset="utf-8">
<title>Keystone Lending – Same Day Tax Advance</title>
<link href="https://fonts.googleapis.com/css2?family=EB+Garamond:wght@600;700&family=Roboto:wght@400;500;700;900&display=swap" rel="stylesheet">
<style>
  :root {
    --green: #157a3c;
    --green-deep: #0d5a2c;
    --red: #c41f26;
    --ink: #222222;
    --muted: #5f5f5f;
    --white: #ffffff;
    --footer: #000000;
    --serif: "EB Garamond", Georgia, serif;
    --sans: "Roboto", Arial, sans-serif;
  }
  * { margin: 0; padding: 0; box-sizing: border-box; }
  html, body { width: 927px; height: 1200px; overflow: hidden; background: var(--white); }
  .flyer { position: relative; width: 927px; height: 1200px; overflow: hidden; font-family: var(--sans); }

  .hero-photo {
    position: absolute; left: 0; top: 0; width: 927px; height: 600px;
    background:
      radial-gradient(ellipse at 80% 38%, #c9a48c 0%, rgba(201,164,140,0) 30%),
      linear-gradient(180deg, #eee9e4 0%, #d9d4cf 16%, #59646f 40%, #4b5661 62%, #7d8ea0 82%, #cfcac4 100%);
  }

  .offer-panel {
    position: absolute; left: 0; top: 0; width: 540px; height: 600px;
    background: linear-gradient(160deg, var(--green) 0%, var(--green-deep) 100%);
    clip-path: polygon(0 0, 540px 0, 450px 600px, 0 600px);
    color: var(--white); font-family: var(--serif);
  }
  .offer-edge {
    position: absolute; left: 0; top: 0; width: 560px; height: 600px;
    background: var(--red);
    clip-path: polygon(540px 0, 556px 0, 466px 600px, 450px 600px);
  }
  .brand-name { position: absolute; left: 56px; top: 58px; font-size: 26px; font-weight: 600; letter-spacing: 0.5px; line-height: 1; }
  .brand-rule { position: absolute; left: 56px; top: 100px; width: 60px; height: 3px; background: var(--red); }
  .offer-day {
    position: absolute; left: 56px; top: 146px;
    background: var(--red); color: var(--white);
    font-size: 60px; font-weight: 700; line-height: 1; padding: 8px 24px 12px;
    border-radius: 6px;
  }
  .offer-line { position: absolute; left: 56px; top: 252px; font-size: 42px; font-weight: 700; line-height: 1; }
  .offer-amount { position: absolute; left: 52px; top: 300px; font-size: 128px; font-weight: 700; line-height: 1; letter-spacing: -1px; }
  .offer-bar { position: absolute; left: 58px; top: 446px; width: 150px; height: 6px; background: var(--red); }

  .apply-stripe { position: absolute; left: 0; top: 600px; width: 927px; height: 8px; background: var(--red); }
  .apply-title { position: absolute; left: 0; width: 927px; top: 636px; text-align: center; font-weight: 900; font-size: 26px; color: var(--red); letter-spacing: 5px; line-height: 1; }
  .apply-amount { position: absolute; left: 0; width: 927px; top: 672px; text-align: center; font-weight: 700; font-size: 60px; color: var(--ink); letter-spacing: -0.5px; line-height: 1.1; }
  .apply-amount .figure { color: var(--green-deep); }

  .pitch { position: absolute; left: 60px; top: 800px; width: 380px; font-size: 24px; font-weight: 500; line-height: 33px; color: var(--muted); }
  .pitch-rule { position: absolute; top: 876px; height: 3px; }
  .pitch-rule.g1 { left: 60px; width: 25px; background: var(--green-deep); }
  .pitch-rule.r { left: 91px; width: 25px; background: var(--red); }
  .pitch-rule.g2 { left: 122px; width: 134px; background: var(--green-deep); }

  .benefits { position: absolute; left: 60px; top: 910px; list-style: none; }
  .benefit { display: flex; align-items: center; height: 40px; margin-bottom: 16px; font-size: 17px; color: var(--muted); }
  .benefit-icon {
    width: 40px; height: 40px; border-radius: 50%; background: var(--white);
    box-shadow: 0 3px 10px rgba(0,0,0,0.14); display: flex; align-items: center; justify-content: center; margin-right: 14px;
  }

  .contact-card {
    position: absolute; left: 494px; top: 790px; width: 384px; height: 320px;
    border: 3px solid var(--green-deep); border-top: 8px solid var(--red);
    border-radius: 24px; background: var(--white);
    box-shadow: 0 8px 24px rgba(0,0,0,0.10);
    text-align: center; color: var(--muted); font-size: 15px;
  }
  .contact-title { padding-top: 30px; font-family: var(--serif); font-weight: 700; font-size: 34px; color: var(--ink); line-height: 1.1; }
  .contact-icon { display: block; margin: 20px auto 0; }
  .contact-address { margin-top: 10px; line-height: 28px; padding: 0 40px; }
  .contact-phone { margin-top: 8px; }

  .site-footer { position: absolute; left: 0; top: 1143px; width: 927px; height: 57px; background: var(--footer); color: var(--white); }
  .copyright { position: absolute; left: 60px; top: 19px; font-size: 15px; }
  .social { position: absolute; left: 787px; top: 18px; display: flex; gap: 10px; }
  .social span { width: 20px; height: 20px; border-radius: 3px; background: var(--white); }
</style>
</head>
<body>
<main class="flyer">
  <div class="hero-photo" role="img" aria-label="Photo of a relaxed woman sitting on the living room floor against a grey sofa with a laptop on her lap"></div>

  <div class="offer-edge" aria-hidden="true"></div>
  <section class="offer-panel">
    <div class="brand-name">Keystone Lending</div>
    <span class="brand-rule"></span>
    <div class="offer-day">Same Day</div>
    <div class="offer-line">Tax Advance up to</div>
    <div class="offer-amount">$6,000</div>
    <span class="offer-bar"></span>
  </section>

  <div class="apply-stripe"></div>
  <h1 class="apply-title">APPLY HERE</h1>
  <h2 class="apply-amount">For <span class="figure">$5,000-$6,000</span> Today!</h2>

  <p class="pitch">File your taxes and apply for an easy advance!</p>
  <span class="pitch-rule g1"></span><span class="pitch-rule r"></span><span class="pitch-rule g2"></span>

  <ul class="benefits">
    <li class="benefit">
      <span class="benefit-icon"><svg width="26" height="26" viewBox="0 0 24 24"><circle cx="12" cy="12" r="10" fill="none" stroke="var(--green-deep)" stroke-width="2.5"/><path d="M12 6.5 V12 L15.5 14" fill="none" stroke="var(--green-deep)" stroke-width="2" stroke-linecap="round"/></svg></span>
      Available In 24 Hours or less
    </li>
    <li class="benefit">
      <span class="benefit-icon"><svg width="26" height="26" viewBox="0 0 24 24"><path d="M8 3 H14 L12.5 7 H9.5 Z" fill="var(--green-deep)"/><path d="M9 8 H13 C17 10 18 14 16 19 H6 C4 14 5 10 9 8 Z" fill="var(--green-deep)"/><circle cx="17" cy="17" r="4" fill="#fff" stroke="var(--green-deep)" stroke-width="1.5"/></svg></span>
      Choose your loan amount
    </li>
    <li class="benefit">
      <span class="benefit-icon"><svg width="26" height="26" viewBox="0 0 24 24"><circle cx="12" cy="12" r="9" fill="none" stroke="var(--green-deep)" stroke-width="4" stroke-dasharray="3.5 2.6"/><circle cx="12" cy="12" r="7" fill="var(--green-deep)"/><path d="M8.5 12 L11 14.5 L15.5 9.5" fill="none" stroke="#fff" stroke-width="1.8"/></svg></span>
      Quick and easy
    </li>
  </ul>

  <section class="contact-card">
    <h3 class="contact-title">Contact Us Today!</h3>
    <svg class="contact-icon" width="22" height="30" viewBox="0 0 22 30" aria-hidden="true"><path d="M11 0 C4.9 0 0 4.9 0 11 C0 19 11 30 11 30 C11 30 22 19 22 11 C22 4.9 17.1 0 11 0 Z" fill="var(--red)"/><circle cx="11" cy="10.5" r="4" fill="#fff"/></svg>
    <p class="contact-address">Address Line 1, Address Line 2, Address Line 3</p>
    <svg class="contact-icon" width="28" height="28" viewBox="0 0 24 24" aria-hidden="true"><path d="M6.6 10.8 C8 13.6 10.4 16 13.2 17.4 L15.4 15.2 C15.7 14.9 16.1 14.8 16.4 15 C17.5 15.4 18.8 15.6 20 15.6 C20.6 15.6 21 16 21 16.6 V20 C21 20.6 20.6 21 20 21 C10.6 21 3 13.4 3 4 C3 3.4 3.4 3 4 3 H7.5 C8.1 3 8.5 3.4 8.5 4 C8.5 5.3 8.7 6.5 9.1 7.6 C9.2 7.9 9.1 8.3 8.9 8.6 Z" fill="var(--red)"/></svg>
    <p class="contact-phone">Contact Number: +1 888 888 8888</p>
  </section>

  <footer class="site-footer">
    <p class="copyright">© Copyright 2023 | All Rights Reserved</p>
    <div class="social" aria-label="Social media links"><span></span><span></span><span></span></div>
  </footer>
</main>
</body>
</html>
```